Home Remodeling company needs a business card design

we need a business card design for home remodeling company in hamilton county, indiana USA. we offers a wide range of construction services including whole house renovations, Design and Build Basements and Kitchen and Bathroom Remodeling . we would like to see designs for both site of business card that use the same color of the company logo and also including all information below :
1- Karim Feltous CEO / General Contractor
2- all company contacts Telephone numbers ( 1-888-DULOM-47 ) ( 317-555-0193) email address ( info@dulomhome.com) website ( www.dulomhome.com ) and social media logos (Facebook- twitter- google plus )
3- company logo
4- licensed . insured . bonded

```html
<!DOCTYPE html>
<html lang="en">
<head>
<meta charset="utf-8">
<title>Dulom Home Remodeling – Business Card</title>
<link rel="stylesheet" href="https://fonts.googleapis.com/css2?family=Arimo:wght@400&family=Open+Sans:wght@400&display=swap">
<style>
  :root {
    --backdrop: #1c1c1d;
    --card-white: #ffffff;
    --brand-red: #c8323a;
    --brand-charcoal: #3a3a3c;
    --panel-grey: #838386;
    --rule-dark: #4a4a4c;
    --ink: #111111;
  }
  * { margin: 0; padding: 0; box-sizing: border-box; }
  html, body {
    width: 1189px; height: 1200px; overflow: hidden;
    background: var(--backdrop);
    font-family: "Arimo", Arial, sans-serif;
  }
  .card {
    position: absolute; left: 140px; width: 916px; height: 524px;
    background: var(--card-white); overflow: hidden;
  }
  .card--front { top: 45px; }
  .card--back { top: 623px; }

  .company-name {
    position: absolute; left: 0; width: 100%;
    display: flex; align-items: center; justify-content: center; gap: 22px;
    color: var(--brand-charcoal);
    font-family: "Arimo", Arial, sans-serif; font-weight: 400;
    font-size: 56px; line-height: 64px; white-space: nowrap;
  }
  .company-name__mark {
    width: 26px; height: 26px; background: var(--brand-red); flex: none;
  }
  .card--front .company-name { top: 92px; }
  .card--back .company-name { top: 206px; }

  .credentials-band {
    position: absolute; left: 0; top: 249px; width: 100%; height: 52px;
    background: var(--brand-red);
    border-top: 3px solid var(--rule-dark);
    border-bottom: 3px solid var(--rule-dark);
    color: #fff; text-align: center;
    font-family: "Open Sans", Arial, sans-serif; font-size: 33px; line-height: 44px;
  }
  .contact-panel {
    position: absolute; left: 0; top: 301px; width: 100%; height: 223px;
    background: var(--panel-grey);
  }
  .person { position: absolute; right: 532px; top: 30px; text-align: right; }
  .person__name { color: var(--brand-red); font-size: 39px; line-height: 44px; }
  .person__role { color: var(--ink); font-size: 25.5px; line-height: 36px; }
  .panel-divider {
    position: absolute; left: 421px; top: 27px; width: 2px; height: 176px;
    background: #444446;
  }
  .contact-list { position: absolute; left: 448px; top: 34px; list-style: none; }
  .contact-list li {
    display: flex; align-items: center; height: 41px;
    color: var(--ink); font-size: 25.5px;
  }
  .contact-list svg { width: 22px; height: 20px; margin-right: 28px; flex: none; }

  .social-row { position: absolute; left: 314px; top: 359px; display: flex; gap: 17px; }
  .social-tile { width: 86px; height: 88px; border-radius: 6px; }
  .social-tile--one { background: #34569a; }
  .social-tile--two { background: #2a9bd6; }
  .social-tile--three { background: var(--brand-red); }
</style>
</head>
<body>

<section class="card card--front">
  <div class="company-name"><span class="company-name__mark"></span>Dulom Home Remodeling</div>

  <div class="credentials-band">licensed . insured . bonded</div>

  <div class="contact-panel">
    <div class="person">
      <p class="person__name">Karim Feltous</p>
      <p class="person__role">CEO / General Contractor</p>
    </div>
    <div class="panel-divider"></div>
    <ul class="contact-list">
      <li>
        <svg viewBox="0 0 22 20"><rect width="22" height="20" rx="2" fill="var(--brand-red)"/><path d="M5 8c0-3 12-3 12 0v1h-3V8H8v1H5z M7 10h8l1 6H6z" fill="#fff"/></svg>
        1-888-DULOM-47
      </li>
      <li>
        <svg viewBox="0 0 22 20"><rect width="22" height="20" rx="2" fill="var(--brand-red)"/><path d="M5 8c0-3 12-3 12 0v1h-3V8H8v1H5z M7 10h8l1 6H6z" fill="#fff"/></svg>
        317-555-0193
      </li>
      <li>
        <svg viewBox="0 0 22 20"><rect width="22" height="20" rx="2" fill="var(--brand-red)"/><circle cx="11" cy="10" r="6" fill="none" stroke="#fff" stroke-width="1.6"/><path d="M5 10h12M11 4v12" stroke="#fff" stroke-width="1.2"/></svg>
        www.dulomhome.com
      </li>
      <li>
        <svg viewBox="0 0 22 20"><rect width="22" height="20" rx="2" fill="var(--brand-red)"/><rect x="4" y="5" width="14" height="10" fill="none" stroke="#fff" stroke-width="1.5"/><path d="M4 5l7 6 7-6" fill="none" stroke="#fff" stroke-width="1.5"/></svg>
        info@dulomhome.com
      </li>
    </ul>
  </div>
</section>

<section class="card card--back">
  <div class="company-name"><span class="company-name__mark"></span>Dulom Home Remodeling</div>

  <div class="social-row">
    <div class="social-tile social-tile--one" role="img" aria-label="Social network profile link"></div>
    <div class="social-tile social-tile--two" role="img" aria-label="Social network profile link"></div>
    <div class="social-tile social-tile--three" role="img" aria-label="Social network profile link"></div>
  </div>
</section>

</body>
</html>
```